Automotive eCommerce Business looking for a business card design

Looking for a clean and simple business card design. Our company name is "Brindle Auto" and we are a company specializing in the ecommerce sales of automotive parts, specifically for pick up trucks and large SUVs. Our company colours are red, black, and white.

Feel free to use the logo provided or create a new logo that you seem fit. Looking forward to your creative ideas!

Industry/Entity Type

Automotive

Contact Information for Business Card

We were thinking of a possibly two-sided design featuring just the logo and company name on one side, and personal information on the other side. Single sided designs will be considered as well.

Font styles to use
Serif
Sans Serif
Decorative

Colors
ec1f27
ffffff
000000

Requirements
Must have
• Space for employee's name, title, phone number and email address, along with the company address and website somewhere.

```html
<!DOCTYPE html>
<html lang="en">
<head>
<meta charset="utf-8">
<title>Brindle Auto – Business Card</title>
<link rel="stylesheet" href="https://fonts.googleapis.com/css2?family=Open+Sans:wght@400;700&display=swap">
<style>
  :root {
    --page-bg: #e9e7e4;
    --card-black: #000000;
    --brand-red: #a81e24;
    --panel-white: #f3f3f3;
    --panel-shade: #dcdcdc;
    --text-light: #ffffff;
    --text-dark: #111111;
  }
  * { margin: 0; padding: 0; box-sizing: border-box; }
  html, body {
    width: 1200px;
    height: 900px;
    overflow: hidden;
    background: var(--page-bg);
  }
  .business-card {
    position: absolute;
    left: 100px;
    top: 150px;
    width: 1000px;
    height: 600px;
    background: var(--card-black);
    overflow: hidden;
    font-family: "Open Sans", Arial, sans-serif;
    color: var(--text-light);
  }
  .brand-band {
    position: absolute;
    right: 0;
    top: 0;
    width: 330px;
    height: 100%;
    background: var(--brand-red);
  }
  .holder-name {
    position: absolute;
    left: 54px;
    top: 70px;
    font-weight: 700;
    font-size: 33px;
    letter-spacing: 0.3px;
    text-transform: uppercase;
    line-height: 1.1;
  }
  .holder-title {
    position: absolute;
    left: 54px;
    top: 110px;
    font-size: 25px;
    line-height: 1.2;
  }
  .contact-list {
    position: absolute;
    left: 54px;
    top: 352px;
    list-style: none;
    font-size: 25px;
    line-height: 37px;
  }
  .contact-list li {
    display: flex;
    align-items: center;
    gap: 12px;
  }
  .contact-icon {
    width: 17px;
    height: 17px;
    fill: var(--text-light);
    flex: none;
  }
  .postal-address {
    position: absolute;
    left: 54px;
    top: 478px;
    font-size: 25px;
    line-height: 37px;
    font-style: normal;
  }
  .brand-panel {
    position: absolute;
    left: 405px;
    top: 40px;
    width: 545px;
    height: 520px;
  }
  .brand-square {
    position: absolute;
    left: 570px;
    top: 145px;
    width: 196px;
    height: 196px;
    background: var(--brand-red);
    border-radius: 26px;
  }
  .brand-name {
    position: absolute;
    left: 405px;
    top: 378px;
    width: 530px;
    text-align: center;
    font-weight: 700;
    font-size: 46px;
    line-height: 1.2;
    color: var(--text-dark);
    white-space: nowrap;
  }
</style>
</head>
<body>
  <div class="business-card">
    <div class="brand-band"></div>

    <p class="holder-name">Daniel Harper</p>
    <p class="holder-title">Managing Director</p>

    <ul class="contact-list">
      <li>
        <svg class="contact-icon" viewBox="0 0 24 24" aria-hidden="true"><path d="M6.6 10.8a15.2 15.2 0 0 0 6.6 6.6l2.2-2.2a1 1 0 0 1 1-.25 11.4 11.4 0 0 0 3.6.57 1 1 0 0 1 1 1V20a1 1 0 0 1-1 1A17 17 0 0 1 3 4a1 1 0 0 1 1-1h3.5a1 1 0 0 1 1 1c0 1.25.2 2.45.57 3.57a1 1 0 0 1-.25 1z"/></svg>
        <span>(044)718203956</span>
      </li>
      <li>
        <svg class="contact-icon" viewBox="0 0 24 24" aria-hidden="true"><path d="M2 5h20v14H2z M4 7v.4l8 5 8-5V7l-8 5z" fill-rule="evenodd"/></svg>
        <span>daniel@brindle.com</span>
      </li>
      <li>
        <svg class="contact-icon" viewBox="0 0 24 24" aria-hidden="true"><circle cx="12" cy="12" r="10"/><path d="M2 12h20M12 2c3 3 3 17 0 20M12 2c-3 3-3 17 0 20" stroke="#000" stroke-width="1.6" fill="none"/></svg>
        <span>www.brindleparts.com</span>
      </li>
    </ul>

    <address class="postal-address">58, Kestrel Park Road,<br>Fairhaven, UK 40213</address>

    <svg class="brand-panel" viewBox="0 0 545 520" aria-hidden="true">
      <defs>
        <linearGradient id="panelFill" x1="0" y1="0" x2="1" y2="1">
          <stop offset="0" stop-color="#f3f3f3"/>
          <stop offset="1" stop-color="#dcdcdc"/>
        </linearGradient>
      </defs>
      <polygon points="272,40 505,150 505,370 272,480 40,370 40,150"
               fill="url(#panelFill)" stroke="url(#panelFill)"
               stroke-width="70" stroke-linejoin="round"/>
    </svg>

    <div class="brand-square" aria-hidden="true"></div>
    <p class="brand-name">Brindle Auto Ltd</p>
  </div>
</body>
</html>
```